Business Card for Beach theme sports bar called MORVIN

I need a business card designed for our employees, front and back. This will be used by the employees of two business locations to hand out to customers. I've attached the previous business cards we used at one time for a Dantells (it is now Morvin). Looking for a fresh new card that is elegant but has character.

Target Market(s)

30-60, middle class

Contact Information for Business Card

We are a beach bar and sports bar. I am looking for an elegant business card with the front to have the MORVIN logo. Then on the back I need it to allow a space for employees to write their names and for them to write in their schedule. I have attached our old cards with our old name Dantells so you can pull everything we need on the cards. one thing is missing is we have another location at 2615 W Calder Ridge Rd with a number of 702-418-9053. Since we will use it for both locations it should allow the employee to circle or check mark the bar which they work at.

Font styles to use
Sans Serif

Requirements
Must have
• We are looking for some fresh ideas for the business card. Something that will really stick out to customers when the staff hands them out. Creativity will be looked at positively, but we still want it to look upscale and fun.

```html
<!DOCTYPE html>
<html lang="en">
<head>
<meta charset="utf-8">
<title>Morvin – Business Card</title>
<link href="https://fonts.googleapis.com/css2?family=Arimo:wght@400;700&family=Tinos:ital@0;1&display=swap" rel="stylesheet">
<style>
  :root {
    --page-bg: #e4e4e4;
    --front-dark: #1b1a1a;
    --front-mid: #3b3a3a;
    --brand-white: #ffffff;
    --brand-red: #e0242a;
    --accent-yellow: #f7c600;
    --ink-grey: #8c8c8c;
    --ink-soft: #8a8a8a;
    --back-bg: #f4f5f3;
  }
  * { margin: 0; padding: 0; box-sizing: border-box; }
  html, body { width: 1200px; height: 1200px; overflow: hidden; }
  body { background: var(--page-bg); position: relative; font-family: "Arimo", Arial, sans-serif; }

  .card { position: absolute; left: 246px; width: 707px; height: 404px; }

  /* Front */
  .card-front { top: 179px; overflow: hidden; }
  .front-texture {
    position: absolute; inset: 0;
    background: linear-gradient(90deg, var(--front-dark) 0%, #262525 45%, var(--front-mid) 100%);
  }
  .brand-name {
    position: absolute; left: 0; right: 0; top: 160px;
    text-align: center; color: var(--brand-white);
    font-family: "Arimo", Arial, sans-serif; font-weight: 700; font-size: 92px; line-height: 1;
  }
  .tagline {
    position: absolute; left: 0; right: 0; top: 316px;
    text-align: center; color: var(--brand-red);
    font-family: "Tinos", "Times New Roman", serif; font-size: 30px; line-height: 1;
  }

  /* Back */
  .card-back { top: 617px; background: var(--back-bg); }
  .offer {
    position: absolute; left: 20px; width: 667px; top: 24px;
    color: var(--accent-yellow); font-weight: 700; font-size: 73px; line-height: 1;
    white-space: nowrap; text-align: center;
  }
  .bartender-label {
    position: absolute; left: 38px; top: 118px;
    color: var(--ink-grey); font-weight: 700; font-size: 36px; line-height: 1; letter-spacing: 0.5px;
  }
  .name-box {
    position: absolute; left: 39px; top: 166px; width: 223px; height: 57px;
    border: 3px solid var(--ink-grey);
  }
  .schedule {
    position: absolute; left: 312px; top: 140px; width: 351px;
    display: grid; grid-template-columns: repeat(7, 1fr);
  }
  .schedule-day {
    text-align: center; color: var(--ink-grey); font-weight: 700; font-size: 24px; line-height: 1;
    height: 32px;
  }
  .schedule-box {
    height: 42px; border: 2px solid var(--ink-grey); margin-right: 2px;
  }
  .location {
    position: absolute; text-align: center; color: var(--ink-soft);
    font-family: "Tinos", "Times New Roman", serif; font-size: 21px; line-height: 27px;
  }
  .location-west { left: 60px; width: 240px; top: 270px; line-height: 28px; }
  .location-east { left: 395px; width: 280px; top: 258px; }
  .fine-print {
    position: absolute; left: 0; right: 0; top: 371px; text-align: center;
    color: var(--ink-soft); font-family: "Tinos", "Times New Roman", serif; font-style: italic; font-size: 11.5px;
  }
</style>
</head>
<body>
  <section class="card card-front">
    <div class="front-texture" role="img" aria-label="Dark background with a repeating tropical leaf pattern"></div>
    <div class="brand-name">Morvin</div>
    <div class="tagline">A Gamers Bar</div>
  </section>

  <section class="card card-back">
    <div class="offer">$20 MATCH PLAY</div>
    <div class="bartender-label">Bartender</div>
    <div class="name-box"></div>

    <div class="schedule">
      <div class="schedule-day">M</div><div class="schedule-day">T</div><div class="schedule-day">W</div><div class="schedule-day">Th</div><div class="schedule-day">F</div><div class="schedule-day">Sa</div><div class="schedule-day">Su</div>
      <div class="schedule-box"></div><div class="schedule-box"></div><div class="schedule-box"></div><div class="schedule-box"></div><div class="schedule-box"></div><div class="schedule-box"></div><div class="schedule-box"></div>
    </div>

    <div class="location location-west">2615 W Calder Ridge Rd<br>702-418-9053</div>
    <div class="location location-east">3180 W Harlow Mesa Rd<br>Las Vegas, NV 89146<br>702-531-7264<br>cs@morvinbar.com</div>

    <p class="fine-print">Match play for new slot members, must play total 100 coin.&nbsp; Please see bartender for details.&nbsp; Management reserves all rights</p>
  </section>
</body>
</html>
```